Redesign of business card for Cedar Ridge Mechanical

We are looking for a new design for our business cards for Cedar Ridge Mechanical. We are a plumbing & HVAC construction company, operating on the West Coast of Canada and USA. Logo attached.
Industry/Entity Type
Construction - Plumbing & HVAC
Contact Information for Business Card
Name, address, phone numbers, email, website address
Look and feel
Each slider illustrates characteristics of the customer's brand and the style your logo design should communicate.

```html
<!DOCTYPE html>
<html lang="en">
<head>
<meta charset="UTF-8">
<title>Cedar Ridge Mechanical – Business Card</title>
<link rel="stylesheet" href="https://fonts.googleapis.com/css2?family=Open+Sans:wght@400;600;700&display=swap">
<style>
  :root {
    --page-bg: #e7e1d8;
    --card-frost: #f4f1ec;
    --card-edge: #d9d3ca;
    --ink-dark: #1e1e1e;
    --band-black: #0b0b0b;
    --band-shadow: #8a8580;
    --gold-text: #d8c3a3;
  }
  * { margin: 0; padding: 0; box-sizing: border-box; }
  html, body {
    width: 1200px;
    height: 1047px;
    overflow: hidden;
    background: var(--page-bg);
    font-family: "Open Sans", sans-serif;
  }
  .business-card {
    position: absolute;
    left: 80px;
    top: 242px;
    width: 1040px;
    height: 562px;
    border-radius: 26px;
    background: var(--card-frost);
    border: 1px solid var(--card-edge);
    overflow: hidden;
    box-shadow: 0 12px 40px rgba(60, 50, 40, 0.15);
  }
  .card-swoosh {
    position: absolute;
    inset: 0;
    width: 100%;
    height: 100%;
  }
  .brand-block {
    position: absolute;
    left: 52px;
    top: 150px;
    display: flex;
    align-items: center;
    gap: 18px;
  }
  .brand-mark {
    width: 34px;
    height: 34px;
    background: var(--ink-dark);
  }
  .brand-name {
    font-size: 34px;
    font-weight: 700;
    letter-spacing: 1px;
    color: var(--ink-dark);
    line-height: 1.15;
  }
  .contact-panel {
    position: absolute;
    right: 46px;
    top: 212px;
    text-align: right;
    color: var(--gold-text);
  }
  .person-name {
    font-size: 34px;
    font-weight: 700;
    letter-spacing: 0.5px;
    line-height: 1.2;
  }
  .person-title {
    font-size: 25px;
    font-weight: 400;
    line-height: 1.3;
    margin-bottom: 30px;
  }
  .address-line {
    font-size: 25px;
    line-height: 1.45;
  }
  .address { margin-bottom: 28px; }
  .contact-line {
    display: flex;
    justify-content: flex-end;
    align-items: center;
    gap: 14px;
    font-size: 25px;
    line-height: 1.42;
  }
  .contact-icon {
    width: 20px;
    height: 20px;
    flex: none;
  }
</style>
</head>
<body>
  <div class="business-card">
    <svg class="card-swoosh" viewBox="0 0 1040 562" preserveAspectRatio="none" aria-hidden="true">
      <path d="M150 562 C 420 520, 560 320, 720 170 C 800 100, 880 100, 1040 94 L 1040 120 C 900 122, 820 140, 740 200 C 590 330, 460 520, 230 562 Z" fill="var(--band-shadow)"/>
      <path d="M190 562 C 450 530, 590 330, 760 190 C 840 128, 920 118, 1040 118 L 1040 562 Z" fill="var(--band-black)"/>
    </svg>

    <div class="brand-block">
      <div class="brand-mark"></div>
      <div class="brand-name">CEDAR RIDGE<br>MECHANICAL</div>
    </div>

    <div class="contact-panel">
      <div class="person-name">DANIEL HAYES</div>
      <div class="person-title">Managing Director</div>
      <div class="address">
        <div class="address-line">Your address, City</div>
        <div class="address-line">State, Zip 1234</div>
      </div>
      <div class="contact-line">123 456 789
        <svg class="contact-icon" viewBox="0 0 24 24" aria-hidden="true"><path fill="currentColor" d="M6.6 10.8a15.1 15.1 0 0 0 6.6 6.6l2.2-2.2c.3-.3.7-.4 1-.2 1.1.4 2.3.6 3.6.6.6 0 1 .4 1 1V20c0 .6-.4 1-1 1C10.6 21 3 13.4 3 4c0-.6.4-1 1-1h3.5c.6 0 1 .4 1 1 0 1.3.2 2.5.6 3.6.1.3 0 .7-.2 1z"/></svg>
      </div>
      <div class="contact-line">info@yourgmail.com
        <svg class="contact-icon" viewBox="0 0 24 24" aria-hidden="true"><path fill="currentColor" d="M3 5h18c.6 0 1 .4 1 1v12c0 .6-.4 1-1 1H3c-.6 0-1-.4-1-1V6c0-.6.4-1 1-1zm1 2.3V17h16V7.3l-8 5.2z"/></svg>
      </div>
      <div class="contact-line">www.yourwebsite.com
        <svg class="contact-icon" viewBox="0 0 24 24" aria-hidden="true"><circle cx="12" cy="12" r="9" fill="none" stroke="currentColor" stroke-width="2"/><path d="M3 12h18M12 3c3 3 3 15 0 18M12 3c-3 3-3 15 0 18" fill="none" stroke="currentColor" stroke-width="1.6"/></svg>
      </div>
    </div>
  </div>
</body>
</html>
```